Pine Ledge Traders, LLC- Global Beverage Company with 100% Cold Chain Logistics

Hey All, My Name is Dale, I am a young business owner in a competitive export space, but my niche is that I am shipping all of my beer around the world, "100% Cold Chain". This model is more costly, but it protects the integrity of the beer itself and will give folks in foreign countries the best representation of what US Craft Beer has to offer.

I am not a branding guy and don't claim to be one, I am a salesperson first, and will be referring to all of you to create something great that will be memorable.

I am looking for a basic Business Card Design for my Craft Beer Export company. I sell US Craft Beer in several countries around the globe. Austrailia, China, Taiwan, Chile, France, New Zealand... to name a few.

I am looking for a sleek, modern, and fresh design. Quickly!

Thanks for your consideration!

Cheers,

Dale

Target Market(s)

International

Contact Information for Business Card

Dale Corrigan
Founder- Roaming Hops Guy
Dale@PineLedgeTraders.example
@RoamingHopsGuy- Instagram only
www.Pineledgetraders.example
@PineLedgeTradersAU- Instagram Only

Font styles to use
Serif

Colors
0592cd
ffffff

Requirements
Must have
• Name-
• Title-
• Email-
• Social Media Handle-
• Company Website-
Nice to have
• Nice Logo/ Images on Card
Should not have
• Tacky Beer Images

```html
<!DOCTYPE html>
<html lang="en">
<head>
<meta charset="utf-8">
<title>Pine Ledge Traders – Business Card</title>
<link rel="stylesheet" href="https://fonts.googleapis.com/css2?family=Outfit:wght@500;600&family=Roboto:wght@400&display=swap">
<style>
  :root {
    --stage: #222222;
    --brand-blue: #0592cd;
    --brand-blue-light: #2aa9e2;
    --white: #ffffff;
    --ink: #3a3a3a;
    --faint-grey: #d4d4d4;
    --card-shadow: rgba(0, 0, 0, 0.75);
  }
  * { margin: 0; padding: 0; box-sizing: border-box; }
  html, body {
    width: 1064px; height: 1200px; overflow: hidden;
    background: var(--stage);
  }
  .stage { position: relative; width: 1064px; height: 1200px; }

  .card {
    position: absolute;
    width: 630px; height: 389px;
    box-shadow: 4px 6px 8px var(--card-shadow);
    overflow: hidden;
  }

  /* Front */
  .card--front {
    left: 265px; top: 141px;
    background: var(--white);
    border-radius: 0 195px 195px 0;
  }
  .brand {
    position: absolute; left: 41px; top: 43px;
    display: flex; align-items: center; gap: 16px;
  }
  .brand__square {
    width: 58px; height: 58px; border-radius: 8px;
    background: var(--brand-blue);
  }
  .brand__name {
    font-family: "Outfit", sans-serif; font-weight: 600;
    font-size: 31px; line-height: 30px; letter-spacing: 0.5px;
    color: var(--brand-blue); text-transform: uppercase;
  }
  .faint-mark {
    position: absolute; left: 392px; top: 160px;
    width: 156px; height: 156px; border-radius: 50%;
    background: var(--faint-grey);
  }
  .person { position: absolute; left: 41px; top: 178px; }
  .person__name {
    font-family: "Outfit", sans-serif; font-weight: 500;
    font-size: 27px; color: var(--brand-blue); line-height: 34px;
  }
  .person__title {
    font-family: "Roboto", sans-serif; font-size: 17px;
    color: var(--ink); line-height: 22px;
  }
  .contact {
    position: absolute; left: 42px;
    display: flex; align-items: center; gap: 8px;
    font-family: "Roboto", sans-serif; font-size: 17px; color: var(--ink);
  }
  .contact svg { width: 17px; height: 17px; flex: none; }
  .contact--email { top: 253px; }
  .contact--web { top: 276px; }
  .contact--social { top: 322px; }
  .social-square { width: 20px; height: 20px; background: #3b5998; flex: none; }

  /* Back */
  .card--back {
    left: 234px; top: 584px;
    background: var(--brand-blue);
    border-radius: 195px 0 0 195px;
  }
  .map-area {
    position: absolute; left: 30px; top: 60px; width: 600px; height: 300px;
    background: radial-gradient(ellipse at 50% 45%, var(--brand-blue-light) 0%, rgba(42,169,226,0.55) 55%, rgba(42,169,226,0) 80%);
  }
  .back-brand {
    position: absolute; left: 0; right: 0; top: 130px;
    display: flex; justify-content: center; align-items: center; gap: 14px;
    padding-left: 40px;
  }
  .back-brand__square {
    width: 62px; height: 62px; border-radius: 8px; background: var(--white);
  }
  .back-brand__name {
    font-family: "Outfit", sans-serif; font-weight: 600;
    font-size: 34px; line-height: 34px; color: var(--white);
    text-transform: uppercase; letter-spacing: 0.5px;
  }
  .tagline, .markets {
    position: absolute; left: 0; right: 0; padding-left: 40px;
    text-align: center; color: var(--white); font-family: "Outfit", sans-serif;
  }
  .tagline { top: 256px; font-size: 22px; font-weight: 500; }
  .markets { top: 295px; font-size: 18px; font-weight: 500; }
</style>
</head>
<body>
<main class="stage">
  <section class="card card--front">
    <div class="brand">
      <span class="brand__square"></span>
      <span class="brand__name">Pine Ledge<br>Traders</span>
    </div>
    <div class="faint-mark"></div>
    <div class="person">
      <p class="person__name">Dale Corrigan</p>
      <p class="person__title">Founder - Roaming Hops Guy</p>
    </div>
    <p class="contact contact--email">
      <svg viewBox="0 0 18 18"><rect x="1" y="3" width="16" height="12" fill="#0592cd"/><path d="M1.5 3.5 9 10l7.5-6.5" fill="none" stroke="#fff" stroke-width="1.3"/></svg>
      Dale@PineLedgeTraders.example
    </p>
    <p class="contact contact--web">
      <svg viewBox="0 0 18 18"><circle cx="9" cy="9" r="8" fill="#0592cd"/><path d="M1 9h16M9 1c-3 3-3 13 0 16M9 1c3 3 3 13 0 16" fill="none" stroke="#fff" stroke-width="1.1"/></svg>
      www.Pineledgetraders.example
    </p>
    <p class="contact contact--social">
      <span class="social-square"></span>
      @RoamingHopsGuy
    </p>
  </section>

  <section class="card card--back">
    <div class="map-area" role="img" aria-label="Faint world map in light blue"></div>
    <div class="back-brand">
      <span class="back-brand__square"></span>
      <span class="back-brand__name">Pine Ledge<br>Traders</span>
    </div>
    <p class="tagline">100% Cold Chain Logistics</p>
    <p class="markets">Austrailia | China | Taiwan | Chile | France | New Zealand</p>
  </section>
</main>
</body>
</html>
```